AGP letterhead

We need a letterhead design for our new company based in Los Angeles called "Amber Gate Pictures". We develop film and television projects. We work with investors, financiers, film production companies, film distribution and sales companies as well as studios. We would like to incorporate our logo (see attached) but make the letterhead simple and elegant. We need to include: logo, company address, phone number and company website.
Updates

Hello designers, Thanks for your submissions. For our letterhead, we are looking for something more simple and elegant. No heavy bars or lines. Make it feel light and clean. Not a lot of ink on the page. Use the logo and contact info but think "clean", "streamlined" and mostly white paper. Looking forward to seeing more... thanks! Amber Gate Pictures team

Target Market(s)

Studio executives, talent agents and agencies, financiers, investors.

Industry/Entity Type

It Company

Requirements
Must have
• Amber Gate Pictures logo (see attached). Logo may be cropped and altered appropriately for elegant letterhead design.
• Please include:
• COMPANY ADDRESS:
• Tolvane Arts Park
• 2850 Delmore Street
• Crest Hall, 2nd Floor
• Corvell Bay, CA 90471
• COMPANY WEBSITE:
• www.ambergatepicturesco.example
• COMPANY PHONE NUMBER:
• 555-604-2187

```html
<!DOCTYPE html>
<html lang="en">
<head>
<meta charset="utf-8">
<title>Amber Gate Pictures — Letterhead</title>
<link rel="stylesheet" href="https://fonts.googleapis.com/css2?family=Open+Sans:wght@400;600&display=swap">
<style>
  :root {
    --backdrop: #e6e6e6;
    --paper-top: #ffffff;
    --paper-bottom: #f3f3f3;
    --ink: #555555;
    --brand-blue: #1a8fc9;
    --brand-dark: #0f2a38;
    --rule: #c8c8c8;
    --mark-faint: #ececec;
    --icon-blue: #3a6fb0;
  }
  html, body {
    margin: 0;
    width: 950px;
    height: 1200px;
    overflow: hidden;
    background: var(--backdrop);
    font-family: "Open Sans", sans-serif;
  }
  .letterhead {
    position: absolute;
    left: 51px;
    top: 51px;
    width: 848px;
    height: 1097px;
    background: linear-gradient(160deg, var(--paper-top) 40%, var(--paper-bottom) 100%);
  }
  .brand {
    position: absolute;
    left: 30px;
    top: 25px;
    width: 202px;
    text-align: center;
  }
  .brand-dot {
    display: block;
    width: 102px;
    height: 102px;
    margin: 0 auto;
    border-radius: 50%;
    background: var(--brand-dark);
  }
  .brand-name {
    margin-top: 7px;
    font-size: 15px;
    font-weight: 600;
    letter-spacing: 0.5px;
    color: var(--brand-blue);
    white-space: nowrap;
  }
  .divider {
    position: absolute;
    left: 257px;
    top: 129px;
    width: 1px;
    height: 43px;
    background: var(--rule);
  }
  .address {
    position: absolute;
    left: 286px;
    top: 119px;
    margin: 0;
    font-style: normal;
    font-size: 16px;
    line-height: 30px;
    color: var(--ink);
    white-space: nowrap;
  }
  .watermark {
    position: absolute;
    left: 265px;
    top: 410px;
  }
  .contact {
    position: absolute;
    left: 0;
    right: 0;
    top: 1055px;
    display: flex;
    justify-content: center;
    align-items: center;
    gap: 10px;
    font-size: 19px;
    color: var(--ink);
    white-space: nowrap;
  }
  .contact-item {
    display: flex;
    align-items: center;
    gap: 6px;
  }
  .contact-item svg { width: 17px; height: 17px; }
</style>
</head>
<body>
  <main class="letterhead">
    <header class="brand">
      <span class="brand-dot"></span>
      <div class="brand-name">Amber Gate Pictures</div>
    </header>

    <div class="divider"></div>

    <address class="address">
      Tolvane Arts Park 2850 Delmore Street Crest Hall,<br>
      2nd Floor Corvell Bay, CA 90471
    </address>

    <svg class="watermark" width="314" height="314" viewBox="0 0 314 314" aria-hidden="true">
      <circle cx="157" cy="157" r="156" fill="var(--mark-faint)"/>
    </svg>

    <footer class="contact">
      <span class="contact-item">
        <svg viewBox="0 0 20 20" aria-hidden="true">
          <circle cx="10" cy="10" r="9" fill="none" stroke="var(--icon-blue)" stroke-width="1.3"/>
          <path d="M7 5.5c-1 1-1.2 3 .5 5.5s3.8 4 5 3.6l1-1-1.8-1.8-1 .7c-.8-.4-2-1.8-2.3-2.6l.7-1L7.5 5z" fill="var(--icon-blue)"/>
        </svg>
        555-604-2187
      </span>
      <span class="contact-item">
        <svg viewBox="0 0 20 20" aria-hidden="true">
          <g fill="none" stroke="var(--icon-blue)" stroke-width="1.1">
            <circle cx="10" cy="10" r="8.5"/>
            <ellipse cx="10" cy="10" rx="3.8" ry="8.5"/>
            <line x1="1.5" y1="10" x2="18.5" y2="10"/>
            <line x1="10" y1="1.5" x2="10" y2="18.5"/>
            <path d="M3 5.5h14M3 14.5h14"/>
          </g>
        </svg>
        www.ambergatepicturesco.example
      </span>
    </footer>
  </main>
</body>
</html>
```